Business Card Design for Flood Rescue 360 - Property Restoration Professionals

I need a business card designed for Flood Rescue 360. We are a full-service property restoration solution. Providing water, fire, smoke & storm restoration as well as mold remediation and full remodel or reconstruction to homes and businesses across Dallas-Fort Worth, TX.
Target Market(s)
home and business owners with insurance covered property damage from water, fire or storm related damage
Industry/Entity Type
property restoration
Contact Information for Business Card
Marcus Pelley General Manager Cell: 214-555-0193 Office: 469-555-0148 email: Marcus@FloodRescue360.example services: Water, Fire, Mold, Reconstruction Tagline: Urgency for Your Water Emergency!
Look and feel
Each slider illustrates characteristics of the customer's brand and the style your logo design should communicate.

```html
<!DOCTYPE html>
<html lang="en">
<head>
<meta charset="utf-8">
<title>Flood Rescue 360 – Business Card</title>
<link href="https://fonts.googleapis.com/css2?family=Montserrat:wght@400;500;800&display=swap" rel="stylesheet">
<style>
  :root {
    --brand-blue: #12ade4;
    --ink: #2b2b2b;
    --card-white: #ffffff;
    --card-grey: #6a6a6a;
    --emboss-grey: #4e4e4e;
    --stage: #bdbdbd;
  }
  * { margin: 0; padding: 0; box-sizing: border-box; }
  html, body { width: 1200px; height: 815px; overflow: hidden; }
  body {
    background: var(--stage);
    font-family: "Montserrat", sans-serif;
    display: flex;
    flex-direction: column;
    align-items: center;
    justify-content: center;
    gap: 44px;
  }
  .card {
    position: relative;
    width: 600px;
    height: 343px;
    border-radius: 28px;
    overflow: hidden;
    box-shadow: 0 10px 24px rgba(0,0,0,0.22);
  }

  /* Front */
  .card-front { background: var(--card-white); color: var(--ink); }
  .brand-name {
    position: absolute;
    top: 56px;
    right: 44px;
    font-weight: 500;
    font-size: 26px;
    line-height: 1.2;
    color: var(--brand-blue);
  }
  .side-tab {
    position: absolute;
    left: 0; top: 140px;
    width: 14px; height: 42px;
    background: var(--brand-blue);
  }
  .holder { position: absolute; left: 36px; top: 134px; }
  .holder-name {
    font-weight: 800;
    font-size: 28px;
    color: var(--brand-blue);
    text-transform: uppercase;
    letter-spacing: 0.5px;
  }
  .holder-title { font-size: 15px; font-weight: 500; margin-top: 2px; }
  .divider {
    position: absolute;
    left: 36px; right: 44px; top: 206px;
    height: 2px;
    background: var(--brand-blue);
  }
  .contact-list {
    position: absolute;
    left: 36px; top: 222px;
    list-style: none;
    font-size: 15px;
    line-height: 24px;
  }
  .contact-list li { display: flex; align-items: center; gap: 10px; }
  .contact-list svg { width: 13px; height: 13px; fill: var(--brand-blue); flex: none; }
  .service-list {
    position: absolute;
    right: 44px; top: 222px;
    list-style: none;
    text-align: right;
    font-size: 15px;
    line-height: 22px;
  }
  .service-list li { display: flex; justify-content: flex-end; align-items: center; gap: 8px; }
  .service-list li::after {
    content: "";
    width: 8px; height: 10px;
    background: var(--brand-blue);
    border-radius: 50% 50% 50% 50% / 40% 40% 60% 60%;
  }

  /* Back */
  .card-back {
    background: var(--card-grey);
    display: flex;
    flex-direction: column;
    align-items: center;
    justify-content: center;
    gap: 48px;
  }
  .back-brand {
    font-weight: 500;
    font-size: 36px;
    line-height: 1.2;
    color: var(--emboss-grey);
    text-align: center;
  }
  .tagline {
    color: #ffffff;
    font-size: 17px;
    font-weight: 500;
    letter-spacing: 0.6px;
  }
</style>
</head>
<body>
  <section class="card card-front">
    <p class="brand-name">Flood Rescue 360</p>
    <span class="side-tab"></span>
    <div class="holder">
      <p class="holder-name">Marcus Pelley</p>
      <p class="holder-title">General Manager</p>
    </div>
    <div class="divider"></div>
    <ul class="contact-list">
      <li><svg viewBox="0 0 24 24"><path d="M6.6 10.8a15 15 0 0 0 6.6 6.6l2.2-2.2c.3-.3.7-.4 1-.2 1.1.4 2.3.6 3.6.6.6 0 1 .4 1 1V20c0 .6-.4 1-1 1A17 17 0 0 1 3 4c0-.6.4-1 1-1h3.5c.6 0 1 .4 1 1 0 1.3.2 2.5.6 3.6.1.3 0 .7-.2 1z"/></svg>214-555-0193</li>
      <li><svg viewBox="0 0 24 24"><path d="M7 1h10a2 2 0 0 1 2 2v18a2 2 0 0 1-2 2H7a2 2 0 0 1-2-2V3a2 2 0 0 1 2-2zm0 3v14h10V4z"/></svg>469-555-0148</li>
      <li><svg viewBox="0 0 24 24"><path d="M2 5h20v14H2zm2 2v.5l8 5 8-5V7z"/></svg>Marcus@FloodRescue360.example</li>
      <li><svg viewBox="0 0 24 24"><path d="M12 2a10 10 0 1 0 0 20 10 10 0 0 0 0-20zm6.9 9h-3a15 15 0 0 0-1.4-6 8 8 0 0 1 4.4 6zM12 4.1c.9 1.3 1.7 3.7 1.9 6.9h-3.8c.2-3.2 1-5.6 1.9-6.9zM9.5 5a15 15 0 0 0-1.4 6h-3a8 8 0 0 1 4.4-6zm-4.4 8h3a15 15 0 0 0 1.4 6 8 8 0 0 1-4.4-6zm6.9 6.9c-.9-1.3-1.7-3.7-1.9-6.9h3.8c-.2 3.2-1 5.6-1.9 6.9zm2.5-.9a15 15 0 0 0 1.4-6h3a8 8 0 0 1-4.4 6z"/></svg>www.FloodRescue360.example</li>
    </ul>
    <ul class="service-list">
      <li>Water</li>
      <li>Fire</li>
      <li>Mold</li>
      <li>Reconstruction</li>
    </ul>
  </section>

  <section class="card card-back">
    <p class="back-brand">Flood Rescue 360</p>
    <p class="tagline">Urgency for Your Water Emergency!</p>
  </section>
</body>
</html>
```